Business card por a urban DJ, up scale audience target

Need a sober design, modern, conservative colors but i can consider some options, y play rnb, hip hop, EDM and top40.

Business card for contact and personal info, double sided, use logo attrached please; im 42 so i need a card acording to my age an target audience.

Target Market(s)

Adult people, up scale audience

Industry/Entity Type

Music Download

Contact Information for Business Card

Cel (318) 4207265518 www.lumadrift.com

Requirements
Must have
• open mind
Nice to have
• open mind
Should not have
• DJ

```html
<!DOCTYPE html>
<html lang="en">
<head>
<meta charset="utf-8">
<title>Luma – Business Card</title>
<link rel="stylesheet" href="https://fonts.googleapis.com/css2?family=Jost:wght@300;400;600&display=swap">
<style>
  :root {
    --page-bg: #d9d7d3;
    --card-white: #ffffff;
    --ink: #1a1a1a;
    --band-dark: #151515;
    --band-light: #4a4a4a;
    --band-text: #ffffff;
    --band-text-soft: #e4e4e4;
  }
  * { box-sizing: border-box; margin: 0; padding: 0; }
  html, body {
    width: 1200px;
    height: 950px;
    overflow: hidden;
    background: var(--page-bg);
    font-family: "Jost", "Futura", sans-serif;
  }
  .sheet {
    width: 1200px;
    height: 950px;
    display: flex;
    flex-direction: column;
    align-items: center;
    justify-content: center;
    gap: 40px;
  }
  .card {
    width: 720px;
    height: 411px;
    position: relative;
    box-shadow: 0 6px 18px rgba(0,0,0,0.18);
  }
  .card--front {
    background: var(--card-white);
  }
  .card--back {
    background: var(--band-dark);
  }
  .brand {
    position: absolute;
    left: 0;
    right: 0;
    top: 70px;
    display: flex;
    justify-content: center;
    align-items: center;
    gap: 16px;
  }
  .brand__mark {
    width: 22px;
    height: 22px;
    background: var(--ink);
  }
  .brand__name {
    font-weight: 600;
    font-size: 96px;
    letter-spacing: 6px;
    line-height: 1;
    color: var(--ink);
  }
  .contact-band {
    position: absolute;
    left: 0;
    right: 0;
    top: 250px;
    height: 110px;
    background: linear-gradient(90deg, var(--band-light) 0%, var(--band-dark) 45%, var(--band-dark) 100%);
    padding: 20px 0 0 80px;
    color: var(--band-text);
  }
  .contact-band__name {
    font-size: 30px;
    font-weight: 600;
    letter-spacing: 1px;
    line-height: 1.15;
  }
  .contact-band__role {
    font-weight: 300;
  }
  .contact-band__details {
    margin-top: 8px;
    font-size: 23px;
    font-weight: 300;
    color: var(--band-text-soft);
    letter-spacing: 0.5px;
  }
  .contact-band__divider {
    margin: 0 8px;
  }
</style>
</head>
<body>
  <main class="sheet">
    <section class="card card--front" aria-label="Business card front">
      <div class="brand">
        <span class="brand__mark"></span>
        <span class="brand__name">LUMA</span>
      </div>
      <div class="contact-band">
        <p class="contact-band__name">MARCO VALE <span class="contact-band__role">- CEO/FOUNDER</span></p>
        <p class="contact-band__details">(318) 4207265518<span class="contact-band__divider">|</span>www.lumadrift.com</p>
      </div>
    </section>
    <section class="card card--back" aria-label="Business card back"></section>
  </main>
</body>
</html>
```